Lindqvar Foundation Letterhead

We are a newly established non profit registered in Maryland but operates in Africa, south of the sahara. We offer scholarships to deserving young adults from high school through college. Our color theme for our existing logo is purple, we want a design that is stylish, spellbinding yet a letterhead that projects seriousness. More information on www.thelindqvarfoundation.example

Target Market(s)

High school and college students in sub saharan African as well as our donors in the US

Industry/Entity Type

Non Profit

Font styles to use
Script

Requirements
Must have
• Logo at the top and if possible watermark the logo in the middle of the letterhead, contact address,
Should not have
• NA

```html
<!DOCTYPE html>
<html lang="en">
<head>
<meta charset="utf-8">
<title>Lindqvar Foundation Letterhead</title>
<link href="https://fonts.googleapis.com/css2?family=Questrial&display=swap" rel="stylesheet">
<style>
  :root{
    --purple:#6a3a96;
    --purple-deep:#5b2d86;
    --lavender:#aaa3d6;
    --ink:#4a4a4a;
    --paper:#f4f4f4;
    --backdrop:#d2d1d3;
    --watermark:#e9e9e9;
  }
  html,body{margin:0;padding:0;overflow:hidden;}
  body{width:1200px;height:991px;background:var(--backdrop);position:relative;}
  .letterhead{
    position:absolute;left:262px;top:20px;width:675px;height:951px;
    background:var(--paper);overflow:hidden;
    box-shadow:0 1px 3px rgba(0,0,0,.25);
  }
  .swoosh{position:absolute;display:block;}
  .swoosh--top{left:0;top:0;}
  .swoosh--bottom{right:0;bottom:0;}
  .brand{position:absolute;left:42px;top:60px;display:flex;align-items:center;gap:14px;}
  .brand__mark{width:56px;height:56px;border-radius:50%;border:3px solid var(--lavender);box-sizing:border-box;}
  .brand__name{font-family:'Questrial',sans-serif;font-size:18px;line-height:22px;color:var(--purple);white-space:nowrap;}
  .watermark{position:absolute;left:115px;top:333px;}
  .contact{position:absolute;left:41px;top:904px;font-family:'Questrial',sans-serif;font-size:9.5px;line-height:12px;color:var(--ink);}
  .contact b{color:var(--purple);font-weight:700;}
  .website{position:absolute;right:77px;top:904px;font-family:'Questrial',sans-serif;font-size:9.5px;color:var(--ink);}
  .website b{color:var(--purple-deep);}
</style>
</head>
<body>
<div class="letterhead">
  <svg class="swoosh swoosh--top" width="250" height="48" viewBox="0 0 250 48">
    <defs>
      <linearGradient id="swooshTop" x1="0" x2="1" y1="0" y2="0">
        <stop offset="0" stop-color="#6a3a96"/>
        <stop offset=".45" stop-color="#aaa3d6"/>
        <stop offset="1" stop-color="#6a3a96"/>
      </linearGradient>
    </defs>
    <path d="M0 0H250C190 2 120 4 70 9C30 13 8 25 0 46Z" fill="url(#swooshTop)"/>
  </svg>

  <div class="brand">
    <div class="brand__mark"></div>
    <div class="brand__name">Lindqvar Foundation Inc</div>
  </div>

  <svg class="watermark" width="445" height="445" viewBox="0 0 445 445">
    <circle cx="222.5" cy="222.5" r="215" fill="none" stroke="var(--watermark)" stroke-width="12"/>
  </svg>

  <div class="contact">
    240 Harbour Lane - Suite 12, Annapolis, MD 21401<br>
    <b>Tel:</b> (410) 555-0148 · <b>Email:</b> info@thelindqvarfoundation.example
  </div>
  <div class="website">www.<b>thelindqvarfoundation</b>.example</div>

  <svg class="swoosh swoosh--bottom" width="340" height="80" viewBox="0 0 340 80">
    <defs>
      <linearGradient id="swooshBottom" x1="0" x2="1" y1="0" y2="0">
        <stop offset="0" stop-color="#6a3a96"/>
        <stop offset=".6" stop-color="#aaa3d6"/>
        <stop offset="1" stop-color="#6a3a96"/>
      </linearGradient>
    </defs>
    <path d="M0 80C80 72 200 70 270 66C315 62 335 40 340 0V80Z" fill="url(#swooshBottom)"/>
  </svg>
</div>
</body>
</html>
```